Home Security Company Business Card

Looking for a eye catching business card that is non traditional and stands out but yet still looks professional. It should include all the pertinent information such as name, title, address, telephone, e-mail, website address should definitely stand out and then finally the logo.

Target Market(s)

Residential and Commercial accounts mostly upscale accounts

Industry/Entity Type

Security

Contact Information for Business Card

Name
Title
Address
Office #
Cell #
E-mail
Website

Font styles to use
Serif
Sans Serif

Requirements
Must have
• Logo, two sided color configuration
Nice to have
• You decide
Should not have
• There really aren't any.

```html
<!DOCTYPE html>
<html lang="en">
<head>
<meta charset="utf-8">
<title>Keystead Security Systems Inc. – Business Card</title>
<link rel="stylesheet" href="https://fonts.googleapis.com/css2?family=Open+Sans:wght@400;600;700&family=Tinos&display=swap">
<style>
  :root {
    --backdrop: #4a3526;
    --card: #ffffff;
    --maroon: #7a1a12;
    --maroon-deep: #5e120c;
    --gold: #e2a93b;
    --gold-light: #f7d77a;
    --ink: #6b1710;
  }
  * { margin: 0; padding: 0; box-sizing: border-box; }
  html, body { width: 1200px; height: 750px; overflow: hidden; }
  body {
    position: relative;
    background: var(--backdrop);
    font-family: "Open Sans", Arial, sans-serif;
  }
  .card {
    position: absolute;
    top: 200px;
    width: 557px;
    height: 320px;
    background: var(--card);
    border-radius: 18px;
    overflow: hidden;
  }
  .card--front { left: 28px; }
  .card--back { left: 615px; }

  .brand {
    position: absolute;
    display: flex;
    align-items: center;
    gap: 10px;
    font-family: "Tinos", "Times New Roman", serif;
    font-weight: 400;
    color: var(--maroon);
    text-transform: uppercase;
    line-height: 1.05;
  }
  .brand__dot { flex: none; border-radius: 50%; background: var(--gold); }
  .card--front .brand { left: 42px; top: 48px; font-size: 15px; }
  .card--front .brand__dot { width: 60px; height: 60px; }
  .card--back .brand { left: 197px; top: 80px; font-size: 25px; }
  .card--back .brand__dot { width: 110px; height: 110px; }

  .person { position: absolute; left: 42px; top: 160px; }
  .person__name {
    font-size: 22px; font-weight: 700; color: var(--maroon); letter-spacing: 0.2px;
  }
  .person__title {
    display: flex; align-items: center; gap: 4px;
    font-size: 15px; color: var(--gold); line-height: 1; margin-top: 1px;
  }
  .person__rule {
    width: 350px; height: 1px;
    background: linear-gradient(90deg, var(--maroon), rgba(122,26,18,0.15));
  }

  .contacts { position: absolute; left: 42px; top: 214px; list-style: none; }
  .contacts li {
    display: flex; align-items: center; gap: 8px;
    font-size: 15px; font-weight: 600; color: var(--ink);
    height: 19px;
  }
  .contacts svg { width: 12px; height: 12px; fill: var(--gold); flex: none; }

  .accent-panel { position: absolute; top: 0; height: 100%; }
  .card--front .accent-panel {
    right: 0; width: 107px;
    background: linear-gradient(90deg, var(--gold) 0%, var(--gold-light) 45%, var(--gold) 80%, var(--maroon) 100%);
  }
  .card--back .accent-panel {
    left: 0; width: 105px;
    background: linear-gradient(90deg, var(--gold) 0%, var(--maroon) 30%, var(--maroon-deep) 100%);
  }

  .website {
    position: absolute; left: 0; right: 0; top: 254px;
    padding-left: 105px;
    text-align: center;
    font-size: 15px; font-weight: 700; color: var(--ink);
  }
</style>
</head>
<body>

<section class="card card--front">
  <div class="brand">
    <span class="brand__dot"></span>
    <span>Keystead<br>Security Systems Inc.</span>
  </div>

  <div class="person">
    <h1 class="person__name">Marcus Hallberg</h1>
    <p class="person__title">Owner <span class="person__rule"></span></p>
  </div>

  <ul class="contacts">
    <li>
      <svg viewBox="0 0 12 12" aria-hidden="true"><path d="M1 4c0-2 2-3 5-3s5 1 5 3l-2 1-1-1V3H4v1L3 5zM3 6h6l1 5H2z"/></svg>
      +330 2471-5536
    </li>
    <li>
      <svg viewBox="0 0 12 12" aria-hidden="true"><path d="M2 1l2-1 2 3-1.5 1.5c.7 1.6 1.8 2.7 3.4 3.4L9.5 6.5l3 2-1 2C6 11 1 6 2 1z"/></svg>
      +3302588-41207
    </li>
    <li>
      <svg viewBox="0 0 12 12" aria-hidden="true"><path d="M0 2h12v8H0zM1.2 3v.4L6 6.6l4.8-3.2V3L6 6z" fill-rule="evenodd"/></svg>
      info@marcushallbergmail.com
    </li>
    <li>
      <svg viewBox="0 0 12 12" aria-hidden="true"><path d="M6 0a4 4 0 0 1 4 4c0 3-4 8-4 8S2 7 2 4a4 4 0 0 1 4-4zm0 2.3a1.7 1.7 0 1 0 0 3.4 1.7 1.7 0 0 0 0-3.4z" fill-rule="evenodd"/></svg>
      228 Larkin Avenue Elgin, Illinois 60123
    </li>
  </ul>

  <div class="accent-panel" role="img" aria-label="Large gold and maroon brand decoration"></div>
</section>

<section class="card card--back">
  <div class="accent-panel" role="img" aria-label="Large maroon and gold brand decoration"></div>

  <div class="brand">
    <span class="brand__dot"></span>
    <span>Keystead<br>Security Systems Inc.</span>
  </div>

  <p class="website">www.keysteadsecuritysystemsinc.com</p>
</section>

</body>
</html>
```